Junk Removal business needs a small billboard design

We are looking to have a billboard design made that will pop out to motorist passing by. The sign will be 6 foot wide by 4 foot tall. We would like it to say:SHOW US YOUR JUNK! 555-271-0836 BIG OR SMALL... WE HAUL IT ALL VICTORY JUNK REMOVALWe have provided a rough draft sketch photo of how large we would want the text. Preferably we want the text to be very large and use up most of the space and to be seen from far away. Also, there are example photos of the green background color and text colors we would like to incorporate into the design. We would like to add our company logo (Files attached) on the billboard too. Next to the phone number we would like to add the camera icon (example photos attached) Thank you in advance for all your hard work!

Font styles to use
Serif
Sans Serif

Requirements
Must have
• Large font that is easy to read from far
• Company name must be large
Nice to have
• Bright and pop out to passing by motorist.

```html
<!DOCTYPE html>
<html lang="en">
<head>
<meta charset="utf-8">
<title>Meadowlark Junk Removal – Billboard</title>
<link href="https://fonts.googleapis.com/css2?family=Montserrat:wght@700;800;900&display=swap" rel="stylesheet">
<style>
  :root {
    --backdrop: #b4b4b4;
    --board-green: #d2f386;
    --ink: #111111;
    --accent-orange: #f05a30;
    --camera-brown: #c45a2c;
    --camera-top: #e9e4da;
    --lens-grey: #5c5c5c;
    --white: #ffffff;
    --badge-tan: #cbbf94;
  }
  html, body {
    margin: 0;
    padding: 0;
    width: 1200px;
    height: 1000px;
    overflow: hidden;
    background: var(--backdrop);
  }
  .billboard {
    display: block;
    width: 1200px;
    height: 1000px;
    font-family: "Montserrat", Arial, sans-serif;
  }
  .board-bg { fill: var(--board-green); }
  .headline-top { fill: var(--ink); font-weight: 800; font-size: 86px; }
  .headline-main {
    fill: var(--accent-orange);
    stroke: var(--ink);
    stroke-width: 7px;
    paint-order: stroke fill;
    stroke-linejoin: round;
    font-weight: 900;
    font-size: 292px;
  }
  .phone-number { fill: var(--ink); font-weight: 800; font-size: 98px; }
  .ribbon { fill: var(--accent-orange); }
  .ribbon-text { fill: var(--white); font-weight: 800; font-size: 45px; }
  .footer-band { fill: var(--ink); }
  .footer-edge { fill: none; stroke: var(--accent-orange); stroke-width: 6px; }
  .company-name { fill: var(--white); font-weight: 800; font-size: 46px; }
  .brand-mark { fill: var(--badge-tan); }
  .brand-name { fill: var(--accent-orange); font-weight: 800; font-size: 25px; }
  .cam-body { fill: var(--camera-brown); stroke: var(--ink); stroke-width: 3px; }
  .cam-top { fill: var(--camera-top); stroke: var(--ink); stroke-width: 3px; }
  .cam-lens-outer { fill: var(--camera-top); stroke: var(--ink); stroke-width: 3px; }
  .cam-lens-inner { fill: var(--lens-grey); stroke: var(--ink); stroke-width: 3px; }
  .cam-glint { fill: var(--white); }
</style>
</head>
<body>
<svg class="billboard" viewBox="0 0 1200 1000" xmlns="http://www.w3.org/2000/svg">
  <rect class="board-bg" x="78" y="152" width="1044" height="696"/>

  <text class="headline-top" x="600" y="248" text-anchor="middle" textLength="724" lengthAdjust="spacingAndGlyphs">SHOW US YOUR</text>
  <text class="headline-main" x="600" y="477" text-anchor="middle" textLength="960" lengthAdjust="spacingAndGlyphs">JUNK !</text>

  <g class="camera-icon">
    <rect class="cam-top" x="214" y="512" width="92" height="30" rx="8"/>
    <rect class="cam-top" x="244" y="503" width="36" height="14" rx="4"/>
    <rect class="cam-body" x="210" y="528" width="100" height="50" rx="8"/>
    <circle class="cam-lens-outer" cx="256" cy="543" r="26"/>
    <circle class="cam-lens-inner" cx="256" cy="543" r="16"/>
    <circle class="cam-glint" cx="250" cy="537" r="4"/>
  </g>
  <text class="phone-number" x="334" y="578" textLength="666" lengthAdjust="spacingAndGlyphs">555-271-0836</text>

  <polygon class="ribbon" points="130,603 1070,603 1048,636 1070,668 130,668 152,636"/>
  <text class="ribbon-text" x="604" y="652" text-anchor="middle" textLength="868" lengthAdjust="spacingAndGlyphs">BIG OR SMALL...WE HAUL IT ALL</text>

  <polygon class="footer-band" points="78,678 296,678 350,754 1122,754 1122,848 78,848"/>
  <polyline class="footer-edge" points="78,678 296,678 350,754 1122,754"/>

  <g class="brand">
    <circle class="brand-mark" cx="168" cy="764" r="38"/>
    <text class="brand-name" x="214" y="773">Meadowlark</text>
  </g>

  <text class="company-name" x="1068" y="822" text-anchor="end" textLength="640" lengthAdjust="spacingAndGlyphs">MEADOWLARK JUNK REMOVAL</text>
</svg>
</body>
</html>
```